Lumavento business card

We need a modern business card - With our 4 colors - See web: www.lumavento.dk

I have attached logo and som old business Cards we have - Lets Make the new ones shine...:-) -

Industry/Entity Type

Business

Requirements
Must have
• the logo with lumavento only,

```html
<!DOCTYPE html>
<html lang="da">
<head>
<meta charset="utf-8">
<title>Lumavento business card</title>
<link rel="stylesheet" href="https://fonts.googleapis.com/css2?family=Arimo:wght@400;700&display=swap">
<style>
  :root {
    --stage: #222222;
    --card-dark: #3b3b3b;
    --card-light: #f7f7f7;
    --green: #8cc63f;
    --orange: #e07a1c;
    --ink: #2e2e2e;
    --soft: #c9c9c9;
  }
  * { box-sizing: border-box; margin: 0; padding: 0; }
  html, body { width: 1200px; height: 873px; overflow: hidden; }
  body {
    background: var(--stage);
    font-family: "Arimo", Arial, sans-serif;
    position: relative;
  }
  .card {
    position: absolute;
    width: 560px;
    height: 320px;
    border-radius: 22px;
    overflow: hidden;
  }
  .card--back { left: 70px; top: 90px; background: var(--card-dark); }
  .card--front { left: 570px; top: 460px; background: var(--card-light); }

  .brand {
    position: absolute;
    display: flex;
    align-items: center;
    gap: 12px;
    font-weight: 400;
  }
  .brand__dot {
    width: 22px; height: 22px;
    border-radius: 50%;
    background: var(--green);
  }
  .card--back .brand { left: 150px; top: 112px; font-size: 40px; color: var(--soft); letter-spacing: 3px; }
  .card--back .rule { position: absolute; left: 150px; right: 70px; top: 178px; height: 3px; background: var(--green); }
  .tagline { position: absolute; left: 150px; top: 196px; font-size: 20px; color: var(--soft); letter-spacing: 1px; }

  .card--front .brand { left: 36px; top: 40px; font-size: 26px; color: var(--ink); letter-spacing: 2px; }
  .person { position: absolute; right: 36px; top: 36px; text-align: right; }
  .person__name { font-size: 20px; font-weight: 700; color: var(--orange); }
  .person__role { font-size: 12px; font-weight: 700; color: var(--ink); margin-top: 2px; }
  .card--front .rule { position: absolute; height: 2px; background: var(--green); }
  .rule--upper { left: 36px; right: 36px; top: 100px; }
  .rule--lower { left: 36px; width: 230px; top: 190px; }
  .website { position: absolute; right: 36px; top: 118px; font-size: 15px; font-weight: 700; color: var(--ink); }
  .website span { color: var(--orange); }

  .contact { position: absolute; left: 36px; top: 206px; list-style: none; }
  .contact li {
    display: flex; align-items: center; gap: 12px;
    font-size: 14px; font-weight: 700; color: var(--ink);
    height: 30px;
  }
  .contact svg { width: 16px; height: 16px; flex: none; }
</style>
</head>
<body>
  <section class="card card--back">
    <div class="brand"><span class="brand__dot"></span>lumavento</div>
    <div class="rule"></div>
    <p class="tagline">medier til unge</p>
  </section>

  <section class="card card--front">
    <div class="brand"><span class="brand__dot"></span>lumavento</div>
    <div class="person">
      <p class="person__name">Mette Holm</p>
      <p class="person__role">Director</p>
    </div>
    <div class="rule rule--upper"></div>
    <p class="website">www.<span>lumavento</span>.dk</p>
    <div class="rule rule--lower"></div>
    <ul class="contact">
      <li>
        <svg viewBox="0 0 16 16" aria-hidden="true"><rect x="4" y="1" width="8" height="14" rx="1.5" fill="none" stroke="#e07a1c" stroke-width="1.6"/><line x1="7" y1="12.5" x2="9" y2="12.5" stroke="#e07a1c" stroke-width="1.4"/></svg>
        0412 318 907
      </li>
      <li>
        <svg viewBox="0 0 16 16" aria-hidden="true"><rect x="1" y="3" width="14" height="10" fill="#e07a1c"/><polyline points="1,3 8,9 15,3" fill="none" stroke="#f7f7f7" stroke-width="1.3"/></svg>
        info@lumavento.dk
      </li>
      <li>
        <svg viewBox="0 0 16 16" aria-hidden="true"><path d="M8 1a5 5 0 0 0-5 5c0 4 5 9 5 9s5-5 5-9a5 5 0 0 0-5-5z" fill="#e07a1c"/><circle cx="8" cy="6" r="2" fill="#f7f7f7"/></svg>
        Solsikkevej 14, 2100 København
      </li>
    </ul>
  </section>
</body>
</html>
```